Maranoola Wines - web page for new Australian wine label

We need a landing page for our wine company. Maranoola is a family owned company, we grow the gapes, and make the wine in the Clare valley. Daniel Whitlock is the winemaker and is well known for his style, which is all about the fruit flavour rather than wood or age influences. Maranoola is Abriginal for 2 hills and a water source. We hand pick, hand plunge, foot crush resulting in elegant wine. Little to no additives, minimal filtering, single vineyard wines. Handcrafted with small releases of only the best fruit from carefully selected rows and bunches. The Clare valley is located two hours North of Adelaide, is known for cool climate and slow ripening, resulting in wines that have an elegant mouth feel, with bright colour and outstanding flavours. Our Brookmere vineyard has a Eastern aspect, gathering morning sun and escaping the hot afternoons, and in our opinion is on of the prettiest valleys in the world. Only 1000 cases per annum of the very best handpicked fruit, from the best rows. We hope you enjoy the Maranoola style, the reds are lighter in colour, fruit driven palate, more old world influence and the Riesling is on the dry side with fresh citrus. Minimal additives and filtering, our aim was to make wine with minimal influence from wine making. Handcrafted wines.

Target Market(s)

females 18 - 60 are the ones that buy 70 percent of wine, so whilst men are also a target, its the ladies we seek to appeal to.

Industry/Entity Type

It Company

Number of Pages Required

4 page

Font styles to use
Serif

Requirements
Must have
• Eye catching front page that makes me feel like i am ordering from quality company, that cares for what they do. Easy to use ordering, and delivery instructions.
• postage is $14.90 per case Australia wide.
• www.maranoolawines-example.com
Nice to have
• I want to see a fun and family oriented business that cares for the wine, we dont make a lot, its buckets and feet. But its wine made wanting to be the best in the world, we dont cut corners on quality. Handcrafted
Should not have
• dont really have any thoughts here, looking for all ideas

```html
<!DOCTYPE html>
<html lang="en">
<head>
<meta charset="utf-8">
<title>Maranoola Wines</title>
<link rel="stylesheet" href="https://fonts.googleapis.com/css2?family=Lora:wght@400;500;600&display=swap">
<style>
  :root {
    --white: #ffffff;
    --ink: #222222;
    --grey: #707070;
    --link: #2a7fc9;
    --blue: #1769bd;
    --blue-deep: #0f5aa8;
    --footer: #0e0e0e;
    --footer-base: #050505;
    --vine-dark: #1f2a1a;
    --vine-mid: #3d4f2c;
    --partner: #4a4a4a;
    --serif: "Lora", Georgia, serif;
  }
  * { box-sizing: border-box; margin: 0; padding: 0; }
  html, body { width: 1200px; height: 2507px; overflow: hidden; }
  body { position: relative; background: var(--white); font-family: var(--serif); color: var(--ink); }

  /* Hero */
  .hero { position: absolute; left: 0; top: 0; width: 1200px; height: 627px;
    background: radial-gradient(ellipse at 50% 45%, var(--vine-mid) 0%, var(--vine-dark) 70%, #141a10 100%); }
  .brand { position: absolute; left: 92px; top: 44px; font-size: 40px; font-weight: 400; color: var(--white); }
  .brand-dot { display: inline-block; width: 12px; height: 12px; border-radius: 50%; background: var(--white); margin-right: 10px; vertical-align: middle; }
  .nav { position: absolute; top: 59px; font-size: 15px; color: var(--white); text-transform: uppercase; white-space: nowrap; }
  .nav.active { border-bottom: 1px solid var(--white); padding-bottom: 3px; }
  .login { position: absolute; left: 1033px; top: 53px; width: 77px; height: 30px; border: 1.5px solid var(--white); border-radius: 15px; color: var(--white); font-size: 12px; text-align: center; line-height: 27px; }
  .hero-title { position: absolute; left: 0; width: 1200px; top: 272px; text-align: center; font-size: 54px; font-weight: 400; color: var(--white); letter-spacing: 2px; }
  .hero-sub { position: absolute; left: 0; width: 1200px; top: 352px; text-align: center; font-size: 32px; font-weight: 400; color: var(--white); }
  .arrow { position: absolute; top: 313px; width: 30px; height: 30px; }

  /* Welcome */
  .section-title { position: absolute; left: 0; width: 1200px; text-align: center; font-weight: 400; text-transform: uppercase; }
  .intro { position: absolute; left: 117px; width: 966px; top: 740px; text-align: center; font-size: 14px; line-height: 25px; color: var(--grey); }
  .feature { position: absolute; width: 300px; text-align: center; }
  .feature-photo { width: 180px; height: 180px; border-radius: 50%; margin: 0 auto; border: 4px solid var(--white); box-shadow: 0 0 0 1px #ddd; background: linear-gradient(150deg, #6b7a4e, #3b3a2c 60%, #8a5a3e); }
  .feature-title { margin-top: 22px; font-size: 20px; font-weight: 400; text-transform: uppercase; white-space: nowrap; }
  .feature-text { margin: 14px auto 0; width: 270px; font-size: 13px; line-height: 21px; color: var(--grey); }
  .read-more { display: block; margin-top: 10px; font-size: 14px; color: var(--link); }

  /* Fruit band */
  .fruit-photo { position: absolute; left: 0; top: 1240px; width: 583px; height: 342px; background: linear-gradient(180deg, #b9cde0 0%, #7e8a63 40%, #5a5646 75%, #6d6a62 100%); }
  .fruit-panel { position: absolute; left: 583px; top: 1240px; width: 617px; height: 342px; background: linear-gradient(135deg, var(--blue) 0%, var(--blue-deep) 100%); color: var(--white); }
  .fruit-title { position: absolute; left: 44px; top: 78px; font-size: 24px; font-weight: 400; text-transform: uppercase; }
  .fruit-text { position: absolute; left: 44px; top: 122px; width: 492px; font-size: 14.5px; line-height: 24px; }
  .delivery { position: absolute; left: 40px; top: 254px; font-size: 17px; }

  /* Ordering cards */
  .card { position: absolute; top: 1724px; width: 311px; height: 289px; background: var(--white); box-shadow: 0 1px 5px rgba(0,0,0,.25); text-align: center; }
  .card-photo { height: 167px; }
  .card-title { margin-top: 22px; font-size: 15px; font-weight: 400; text-transform: uppercase; }
  .card-text { margin: 8px auto 0; width: 280px; font-size: 12px; line-height: 18px; color: #555; }
  .card-more { display: block; margin-top: 6px; font-size: 12px; color: var(--link); }

  /* Partners */
  .partner { position: absolute; top: 2124px; width: 180px; text-align: center; font-size: 21px; font-weight: 600; color: var(--partner); }
  .partner-mark { display: inline-block; width: 18px; height: 18px; border-radius: 50%; background: var(--partner); margin-right: 8px; vertical-align: -2px; }

  /* Footer */
  .footer { position: absolute; left: 0; top: 2206px; width: 1200px; height: 219px; background: var(--footer); color: var(--white); }
  .footer-base { position: absolute; left: 0; top: 2425px; width: 1200px; height: 82px; background: var(--footer-base); color: var(--white); text-align: center; font-size: 13px; line-height: 92px; }
  .footer-brand { position: absolute; left: 92px; top: 94px; font-size: 36px; color: var(--white); }
  .footer-head { position: absolute; top: 52px; font-size: 15px; font-weight: 400; text-transform: uppercase; }
  .footer-lines { position: absolute; top: 88px; font-size: 11.5px; line-height: 22px; }
  .subscribe { position: absolute; left: 658px; top: 128px; display: flex; }
  .subscribe-input { width: 147px; height: 29px; background: var(--white); color: #888; font-size: 11px; padding-left: 8px; line-height: 29px; }
  .subscribe-btn { width: 56px; height: 29px; background: #3d8fd6; color: var(--white); font-size: 11px; text-align: center; line-height: 29px; }
  .social { position: absolute; top: 107px; width: 24px; height: 24px; border-radius: 4px; background: var(--white); }
</style>
</head>
<body>

<header class="hero" role="img" aria-label="Vineyard canopy with bunches of dark red grapes among green leaves"></header>
<div class="brand"><span class="brand-dot"></span>Maranoola</div>
<nav>
  <span class="nav active" style="left:503px">Home</span>
  <span class="nav" style="left:590px">About Us</span>
  <span class="nav" style="left:708px">Products</span>
  <span class="nav" style="left:830px">Blog</span>
  <span class="nav" style="left:914px">Contact Us</span>
  <span class="login">LOG IN</span>
</nav>
<h1 class="hero-title">MARANOOLA</h1>
<p class="hero-sub">Handcrafted wines from the Clare Valley</p>
<svg class="arrow" style="left:72px" viewBox="0 0 30 30"><circle cx="15" cy="15" r="15" fill="#000" opacity=".6"/><path d="M17 9l-6 6 6 6" stroke="#fff" stroke-width="2" fill="none"/></svg>
<svg class="arrow" style="left:1105px" viewBox="0 0 30 30"><circle cx="15" cy="15" r="15" fill="#000" opacity=".6"/><path d="M13 9l6 6-6 6" stroke="#fff" stroke-width="2" fill="none"/></svg>

<h2 class="section-title" style="top:690px;font-size:34px">Welcome to Maranoola</h2>
<p class="intro">Maranoola is a family owned winery. We grow the grapes and make the wine in the Clare Valley, two hours north of Adelaide. Winemaker Daniel Whitlock lets the fruit speak, not wood or age: little to no additives, minimal filtering, single vineyard wines.</p>

<div class="feature" style="left:94px;top:841px">
  <div class="feature-photo" role="img" aria-label="Woman in the vineyard holding up a freshly picked bunch of grapes"></div>
  <h3 class="feature-title">We Hand Pick</h3>
  <p class="feature-text">Only the best bunches from carefully selected rows, picked by hand into buckets in the cool of the morning.</p>
  <span class="read-more">Read More -&gt;</span>
</div>
<div class="feature" style="left:440px;top:841px">
  <div class="feature-photo" role="img" aria-label="Family members together in the winery during plunging" style="background:linear-gradient(150deg,#8a7a6a,#3a3230 60%,#b89c88)"></div>
  <h3 class="feature-title">Hand Plunge</h3>
  <p class="feature-text">Small open ferments plunged by hand, so every batch gets the care and attention it deserves.</p>
  <span class="read-more">Read More -&gt;</span>
</div>
<div class="feature" style="left:782px;top:841px">
  <div class="feature-photo" role="img" aria-label="Winemakers working at a steel fermenting tank" style="background:linear-gradient(150deg,#9aa0a4,#4a5058 55%,#7e8890)"></div>
  <h3 class="feature-title">Foot Crush Resulting</h3>
  <p class="feature-text">Feet, not machines. Gentle crushing gives elegant wines with bright colour and true fruit flavour.</p>
  <span class="read-more">Read More -&gt;</span>
</div>

<section>
  <div class="fruit-photo" role="img" aria-label="Picking crew gathered beside a ute at the vineyard"></div>
  <div class="fruit-panel">
    <h2 class="fruit-title">Best Handpicked Fruit</h2>
    <p class="fruit-text">Our Brookmere vineyard faces east, gathering the morning sun and escaping the hot afternoons. Slow ripening gives an elegant mouth feel. Just 1000 cases a year: lighter, fruit driven reds and a dry Riesling with fresh citrus.</p>
    <p class="delivery">Delivery charge is $14.90 per case Australia wide</p>
  </div>
</section>

<h2 class="section-title" style="top:1648px;font-size:28px">How To Order</h2>
<article class="card" style="left:107px">
  <div class="card-photo" role="img" aria-label="Winemaker tipping a bucket of grapes in the vineyard" style="background:linear-gradient(160deg,#9ab4cc,#5f6a6e 55%,#c07a50)"></div>
  <h3 class="card-title">1. Choose Your Wines</h3>
  <p class="card-text">Browse our fruit driven reds and dry Riesling, then add your favourites.</p>
  <span class="card-more">Shop Wines »</span>
</article>
<article class="card" style="left:446px">
  <div class="card-photo" role="img" aria-label="Family gathered in the barrel room" style="background:linear-gradient(160deg,#6e5a48,#3a2e26 55%,#8c7a66)"></div>
  <h3 class="card-title">2. Pick Your Cases</h3>
  <p class="card-text">Mix and match a dozen. Postage is $14.90 per case, Australia wide.</p>
  <span class="card-more">Order Now »</span>
</article>
<article class="card" style="left:785px">
  <div class="card-photo" role="img" aria-label="Winery equipment and a forklift beside the crusher" style="background:linear-gradient(160deg,#b0b2b0,#6a6c6a 55%,#9a9c98)"></div>
  <h3 class="card-title">3. Delivered To Your Door</h3>
  <p class="card-text">Pay securely and we pack your wine at the winery and send it to you.</p>
  <span class="card-more">Delivery Info »</span>
</article>

<div class="partners">
  <span class="partner" style="left:127px"><span class="partner-mark"></span>Vinecraft</span>
  <span class="partner" style="left:319px"><span class="partner-mark"></span>Cellarline</span>
  <span class="partner" style="left:515px"><span class="partner-mark"></span>Barrelworks</span>
  <span class="partner" style="left:710px"><span class="partner-mark"></span>Grapeway</span>
  <span class="partner" style="left:908px"><span class="partner-mark"></span>Oakfield</span>
</div>

<footer class="footer">
  <div class="footer-brand">Maranoola</div>
  <h4 class="footer-head" style="left:359px">Contact Us</h4>
  <p class="footer-lines" style="left:359px">Address : 12 Ridgeway Lane, Clare<br>SA 5453<br>Phone : 08-555-0143<br>Email : hello@maranoolawines-example.com</p>
  <h4 class="footer-head" style="left:658px">Sign Up for Newsletter</h4>
  <p class="footer-lines" style="left:658px;width:230px;line-height:18px">New releases and cellar news, straight to your inbox.</p>
  <div class="subscribe"><span class="subscribe-input">Email address</span><span class="subscribe-btn">Submit</span></div>
  <h4 class="footer-head" style="left:949px">Follow Us Out There</h4>
  <span class="social" style="left:949px"></span>
  <span class="social" style="left:987px"></span>
  <span class="social" style="left:1025px"></span>
  <span class="social" style="left:1063px"></span>
</footer>
<div class="footer-base">Copyright © 2017. All Rights Reserved</div>

</body>
</html>
```